Law firm business card

Information:

Me Mireille Dufontaine

website: dufontaine-legal.ca
email: mireille@dufontaine-legal.ca
Phone: 514 382-5167
Fax: 514 382-5169

Address:
Dufontaine and associates
2719 Belcourtier
Montreal, QC
H2K 3M9

Areas of Expertise:
Franchise Agreements, Financing, Acquisition, Real Estate Development, Commercial Agreements and Corporate Law

Target Market(s)

executives, companie managers

Industry/Entity Type

Business

Colors
f78f20
000000

Requirements
Must have
• Must use the logo, the logo is available here:

https://www.filecrate-example.com/sh/qyt3kwud82mfa0x/BBQTn7Lhvpe_kRTXwJM_GhcYb

```html
<!DOCTYPE html>
<html lang="en">
<head>
<meta charset="utf-8">
<title>Dufontaine and associates — Business Card</title>
<link rel="stylesheet" href="https://fonts.googleapis.com/css2?family=Exo+2:wght@400;500;600&display=swap">
<style>
  :root {
    --brand-orange: #f78f20;
    --ink: #000000;
    --ink-soft: #3a3a3a;
    --card-white: #ffffff;
    --card-shade: #f1f1f1;
    --backdrop: #2b2b2b;
  }
  * { box-sizing: border-box; margin: 0; padding: 0; }
  html, body {
    width: 1200px; height: 857px; overflow: hidden;
    background: var(--backdrop);
    font-family: "Exo 2", sans-serif;
  }
  .stage {
    position: relative; width: 1200px; height: 857px;
    display: flex; justify-content: center; align-items: center; gap: 80px;
  }
  .card {
    position: relative;
    width: 380px; height: 640px;
    background: linear-gradient(160deg, var(--card-white) 55%, var(--card-shade));
    box-shadow: 0 20px 40px rgba(0,0,0,.5);
    overflow: hidden;
  }
  .brand {
    display: flex; flex-direction: column; align-items: center;
    padding-top: 70px;
  }
  .brand-circle {
    width: 84px; height: 84px; border-radius: 50%;
    border: 4px solid var(--brand-orange);
    margin-bottom: 14px;
  }
  .brand-name {
    color: var(--brand-orange);
    font-weight: 500;
    font-size: 30px; letter-spacing: 2px;
    text-transform: uppercase; text-align: center; line-height: 1.1;
  }
  .card-back .brand { padding-top: 120px; }
  .person { margin-top: 80px; }
  .person-name {
    padding-left: 36px;
    color: var(--ink-soft);
    font-size: 27px; font-weight: 600; letter-spacing: 2px;
    text-transform: uppercase;
  }
  .person-title {
    margin-top: 6px; margin-left: 28px;
    background: var(--brand-orange);
    color: var(--card-white);
    font-size: 17px; font-weight: 500; letter-spacing: 2px;
    text-transform: uppercase;
    padding: 6px 10px;
    border-radius: 4px 0 0 4px;
  }
  .address {
    margin: 34px 0 0 36px;
    color: var(--ink-soft);
    font-size: 17px; line-height: 1.35;
  }
  .contact-list {
    list-style: none;
    margin: 36px 0 0 36px;
    color: var(--ink-soft);
    font-size: 13px;
  }
  .contact-list li {
    display: flex; align-items: center; gap: 10px;
    margin-bottom: 10px;
  }
  .contact-list svg { width: 14px; height: 14px; fill: var(--ink-soft); flex: none; }
</style>
</head>
<body>
<main class="stage">
  <section class="card card-front">
    <div class="brand">
      <div class="brand-circle"></div>
      <div class="brand-name">Dufontaine<br>and associates</div>
    </div>
    <div class="person">
      <h1 class="person-name">Mireille Dufontaine</h1>
      <p class="person-title">General Manager</p>
    </div>
    <p class="address">2719 Belcourtier,<br>Montreal, QC H2K 3M9</p>
    <ul class="contact-list">
      <li>
        <svg viewBox="0 0 16 16"><path d="M3 1l3 3-1.5 2a9 9 0 005.5 5.5L12 10l3 3-2 2C7 15 1 9 1 3z"/></svg>
        <span>514 382-5167</span>
      </li>
      <li>
        <svg viewBox="0 0 16 16"><path d="M4 1h8v14H4zM5.5 2.5v9h5v-9z"/><circle cx="8" cy="13.2" r=".8"/></svg>
        <span>514 382-5169</span>
      </li>
      <li>
        <svg viewBox="0 0 16 16"><path d="M1 3h14v10H1zM2 4v.5l6 4 6-4V4z"/></svg>
        <span>mireille@dufontaine-legal.ca</span>
      </li>
      <li>
        <svg viewBox="0 0 16 16"><path d="M8 1a7 7 0 100 14A7 7 0 008 1zm0 1.5c.8 0 1.8 1.7 2 4.5H6c.2-2.8 1.2-4.5 2-4.5zM2.6 7h2.2c.1-1.6.4-3 .9-3.9A5.5 5.5 0 002.6 7zm0 2a5.5 5.5 0 003.1 3.9c-.5-.9-.8-2.3-.9-3.9zM6 9h4c-.2 2.8-1.2 4.5-2 4.5S6.2 11.8 6 9zm5.2 0c-.1 1.6-.4 3-.9 3.9A5.5 5.5 0 0013.4 9zm2.2-2a5.5 5.5 0 00-3.1-3.9c.5.9.8 2.3.9 3.9z"/></svg>
        <span>www.dufontaine-legal.ca</span>
      </li>
    </ul>
  </section>

  <section class="card card-back">
    <div class="brand">
      <div class="brand-circle"></div>
      <div class="brand-name">Dufontaine<br>and associates</div>
    </div>
  </section>
</main>
</body>
</html>
```